Emerging Ed-Tech Startup seeking Stationery Designs!

We are in need of basic set of stationery designs to be used for our business operations, letters, emails, and in-office materials. We are a technology startup enhancing on campus work experience offerings by establishing a collaborative work environment for the completion of such tasks.

Our colors are Vibrant Tiffany Blue/Black/White.

Website: www.campusnorthway.com (Still under construction aside from the landing pages)

Please make sure the designs use a brighter more vibrant tiffany blue color than seen in the image files uploaded. We are not using those materials.

Our logo has been added as a file as well, please use that for any designs (include that logo). Thank you.

```html
<!DOCTYPE html>
<html lang="en">
<head>
<meta charset="utf-8">
<title>Campus Northway Stationery Set</title>
<link rel="stylesheet" href="https://fonts.googleapis.com/css2?family=Jost:wght@400;500;600&family=Arimo&display=swap">
<style>
  :root{
    --tiffany:#0ce6e8;
    --ink:#1a1a1a;
    --paper:#ffffff;
    --backdrop:#9a7650;
    --muted:#555555;
    --faint:#dfe6e8;
    --edge:#6b5a48;
  }
  *{box-sizing:border-box;margin:0;padding:0}
  html,body{width:1200px;height:688px;overflow:hidden}
  body{background:var(--backdrop);font-family:'Jost',sans-serif;color:var(--ink);position:relative}

  .sheet{position:absolute;background:var(--paper);border:1px solid var(--edge);overflow:hidden}
  .side-curve{position:absolute;width:14px;border-radius:50%;background:var(--tiffany)}

  .wordmark{position:absolute;display:flex;align-items:center;gap:6px;font-weight:600;text-transform:uppercase;color:var(--ink);line-height:1.05}
  .wordmark .mark-square{background:var(--tiffany);flex:none}
  .contact{position:absolute;font-size:7px;letter-spacing:.3px;color:var(--ink);line-height:1.7}
  .contact .dot{display:inline-block;width:5px;height:5px;border-radius:50%;background:var(--tiffany);margin-right:4px;vertical-align:middle}
  .contact svg{width:6px;height:7px;margin-right:3px;vertical-align:middle;fill:var(--tiffany)}

  /* Letterhead */
  .letterhead{left:39px;top:23px;width:345px;height:447px}
  .letterhead .wordmark{left:22px;top:20px;font-size:15px;width:120px}
  .letterhead .mark-square{width:16px;height:16px}
  .letterhead .contact{left:236px;top:18px;border-left:1px solid #999;padding-left:6px}
  .letterhead .footer-address{left:120px;top:428px}

  /* Fax */
  .fax{left:421px;top:28px;width:345px;height:447px}
  .fax .wordmark{left:24px;top:16px;font-size:15px;width:120px}
  .fax .mark-square{width:16px;height:16px}
  .fax .header-address{left:252px;top:30px;border-left:1px solid #999;padding-left:4px}
  .fax-title{position:absolute;left:27px;top:94px;font-family:'Arimo',sans-serif;font-size:22px;color:var(--ink)}
  .fax-fields{position:absolute;left:29px;top:137px;width:288px;display:grid;grid-template-columns:186px 102px;row-gap:22px}
  .fax-field{font-family:'Arimo',sans-serif;font-size:8.5px;height:19px;border-bottom:1.3px solid var(--ink)}
  .fax .footer-contact{left:92px;top:427px}

  /* Envelope flaps */
  .flap{left:789px;width:387px;height:166px}
  .flap-band{position:absolute;left:0;top:0;width:100%;height:58px;display:flex;align-items:center;justify-content:center;font-weight:600;font-size:17px;letter-spacing:1px;text-transform:uppercase}
  .flap-white{top:27px}
  .flap-white .flap-band{border-bottom:1px solid var(--edge);color:var(--ink)}
  .flap-black{top:214px;height:167px}
  .flap-black .flap-band{background:var(--ink);color:var(--paper)}
  .flap-tiffany{top:397px}
  .flap-tiffany .flap-band{background:var(--tiffany);color:var(--paper)}

  /* Email signature */
  .signature{left:33px;top:528px;width:366px;height:100px}
  .signature .wordmark{left:12px;top:12px;font-size:11px;width:90px;gap:4px}
  .signature .mark-square{width:11px;height:11px}
  .signature .contact{left:10px;top:55px;line-height:1.8}
  .signer{position:absolute;right:14px;top:37px;text-align:right;text-transform:uppercase}
  .signer-name{font-size:9.5px;font-weight:500;letter-spacing:.3px}
  .signer-role{font-size:7px;font-weight:500;letter-spacing:.3px;margin-top:3px}
  .caption{position:absolute;left:141px;top:646px;font-size:19px;color:#f4f0ea;font-family:'Jost',sans-serif}

  /* Envelope front */
  .envelope{left:460px;top:500px;width:387px;height:166px}
  .envelope .wordmark{left:20px;top:10px;font-size:15px;width:120px}
  .envelope .mark-square{width:16px;height:16px}
  .envelope .header-address{left:14px;top:60px}
  .envelope .footer-web{left:14px;top:144px}
  .faint-name{position:absolute;right:12px;top:124px;font-size:16px;font-weight:600;color:var(--faint);text-transform:uppercase;letter-spacing:1px}
</style>
</head>
<body>

  <!-- Letterhead -->
  <section class="sheet letterhead">
    <div class="wordmark"><span class="mark-square"></span><span>Campus Northway</span></div>
    <div class="contact">
      <div><svg viewBox="0 0 6 7"><path d="M1 0h1.4l.6 1.8-.9.7a4 4 0 0 0 1.6 2l.8-.7L6 5v1.3C6 6.7 5.6 7 5 7 2.3 6.6.3 4.4 0 1.2 0 .5.4 0 1 0z"/></svg>+91 40 5512870</div>
      <div><span class="dot"></span>www.campusnorthway.com</div>
    </div>
    <div class="contact footer-address"><span class="dot"></span>House#B-14 Lake Road</div>
    <span class="side-curve" style="left:-7px;top:127px;height:235px"></span>
    <span class="side-curve" style="right:-7px;top:127px;height:235px"></span>
  </section>

  <!-- Fax sheet -->
  <section class="sheet fax">
    <div class="wordmark"><span class="mark-square"></span><span>Campus Northway</span></div>
    <div class="contact header-address">House#B-14 Lake Road</div>
    <h1 class="fax-title">FAX</h1>
    <div class="fax-fields">
      <div class="fax-field">To</div><div class="fax-field">From</div>
      <div class="fax-field">Fax</div><div class="fax-field">Pages</div>
      <div class="fax-field">Phone</div><div class="fax-field">Date</div>
      <div class="fax-field">Re</div><div class="fax-field">CC</div>
    </div>
    <div class="contact footer-contact">
      <svg viewBox="0 0 6 7"><path d="M1 0h1.4l.6 1.8-.9.7a4 4 0 0 0 1.6 2l.8-.7L6 5v1.3C6 6.7 5.6 7 5 7 2.3 6.6.3 4.4 0 1.2 0 .5.4 0 1 0z"/></svg>+91 40 5512870 &nbsp;<span class="dot"></span>www.campusnorthway.com
    </div>
    <span class="side-curve" style="left:-7px;top:125px;height:240px"></span>
    <span class="side-curve" style="right:-7px;top:125px;height:240px"></span>
  </section>

  <!-- Envelope flaps -->
  <section class="sheet flap flap-white"><div class="flap-band">Campus Northway</div></section>
  <section class="sheet flap flap-black"><div class="flap-band">Campus Northway</div></section>
  <section class="sheet flap flap-tiffany"><div class="flap-band">Campus Northway</div></section>

  <!-- Email signature -->
  <section class="sheet signature">
    <div class="wordmark"><span class="mark-square"></span><span>Campus Northway</span></div>
    <div class="contact">
      <div><svg viewBox="0 0 6 7"><path d="M1 0h1.4l.6 1.8-.9.7a4 4 0 0 0 1.6 2l.8-.7L6 5v1.3C6 6.7 5.6 7 5 7 2.3 6.6.3 4.4 0 1.2 0 .5.4 0 1 0z"/></svg>+91 40 5512870</div>
      <div><svg viewBox="0 0 6 7"><rect x="1" y="0" width="4" height="7" rx="1"/></svg>+91 22 4418093</div>
      <div><span class="dot"></span>www.campusnorthway.com</div>
    </div>
    <div class="signer">
      <div class="signer-name">Mr. Oliver Grant</div>
      <div class="signer-role">Marketing Manager</div>
    </div>
    <span class="side-curve" style="left:-7px;top:20px;height:60px"></span>
    <span class="side-curve" style="right:-7px;top:20px;height:60px"></span>
  </section>
  <div class="caption">Email Signtaure</div>

  <!-- Envelope front -->
  <section class="sheet envelope">
    <div class="wordmark"><span class="mark-square"></span><span>Campus Northway</span></div>
    <div class="contact header-address">House#B-14 Lake Road</div>
    <div class="contact footer-web">www.campusnorthway.com</div>
    <div class="faint-name">Campus Northway</div>
    <span class="side-curve" style="left:-7px;top:35px;height:95px"></span>
    <span class="side-curve" style="right:-7px;top:35px;height:95px"></span>
  </section>

</body>
</html>
```